Upmarket Dessert Lounge needs a Business Card Design

We are an upmarket dessert lounge needing a business card to match our image.

We want something that is simple yet beautiful, feminine, classy, sophisticated and elegant. We want it to stand out and don't mind if it is bold.

The design should include our logo and colours of red or maroon with gold highlights. We don't mind if black is used.

Marlow & Quince

Target Market(s)

For those who like to indulge or treat themselves and give in to their temptations on good quality desserts.

Industry/Entity Type

Business

Requirements
Must have
• Must include our logo and our name

Marlow & Quince

M & Q

```html
<!DOCTYPE html>
<html lang="en">
<head>
<meta charset="utf-8">
<title>Marlow &amp; Quince — Business Card</title>
<link href="https://fonts.googleapis.com/css2?family=Source+Sans+3:wght@400;600;700&display=swap" rel="stylesheet">
<style>
  :root {
    --maroon: #7a1315;
    --gold: #f6d3a0;
    --white: #ffffff;
    --ink: #4a4a4a;
    --backdrop: #ecebe8;
  }
  * { box-sizing: border-box; margin: 0; padding: 0; }
  html, body { width: 1200px; height: 402px; overflow: hidden; }
  body {
    background: var(--backdrop);
    font-family: "Source Sans 3", Arial, sans-serif;
    position: relative;
  }
  .card {
    position: absolute;
    top: 56px;
    width: 510px;
    height: 290px;
    border-radius: 27px;
    overflow: hidden;
  }
  .card--front { left: 62px; background: var(--white); }
  .card--back  { left: 629px; background: var(--maroon); }

  .front__swoosh { position: absolute; inset: 0; }

  .front__person {
    position: absolute;
    right: 40px;
    top: 33px;
    text-align: right;
    color: var(--white);
  }
  .front__name { font-size: 18px; font-weight: 700; line-height: 1.1; }
  .front__title { font-size: 14px; font-weight: 400; }

  .front__brand {
    position: absolute;
    left: 28px;
    top: 108px;
    width: 250px;
    text-align: center;
    color: var(--maroon);
    font-size: 22px;
    font-weight: 600;
    letter-spacing: 1.5px;
    text-transform: uppercase;
  }

  .contact {
    position: absolute;
    left: 38px;
    top: 209px;
    list-style: none;
    font-size: 13px;
    color: var(--ink);
  }
  .contact li { display: flex; align-items: center; height: 17.5px; }
  .contact svg { width: 10px; height: 10px; margin-right: 5px; fill: var(--maroon); }

  .divider {
    position: absolute;
    left: 207px;
    top: 246px;
    width: 1.5px;
    height: 46px;
    background: var(--maroon);
  }
  .address {
    position: absolute;
    left: 221px;
    top: 250px;
    font-size: 13px;
    line-height: 15px;
    color: var(--ink);
    font-style: normal;
  }

  .back__brand {
    position: absolute;
    inset: 0;
    display: flex;
    align-items: center;
    justify-content: center;
    color: var(--gold);
    font-size: 76px;
    font-weight: 600;
    letter-spacing: 2px;
  }
</style>
</head>
<body>
  <section class="card card--front" aria-label="Card front">
    <svg class="front__swoosh" viewBox="0 0 510 290" preserveAspectRatio="none" aria-hidden="true">
      <path d="M0,0 H510 V176 C420,100 260,52 0,48 Z" fill="var(--maroon)"/>
      <path d="M0,36 C120,18 230,28 330,74" fill="none" stroke="var(--white)" stroke-width="3"/>
    </svg>
    <div class="front__person">
      <p class="front__name">Your name</p>
      <p class="front__title">Title</p>
    </div>
    <p class="front__brand">Marlow &amp; Quince</p>

    <ul class="contact">
      <li><svg viewBox="0 0 10 10"><path d="M2,0 L4,2 L3,3.5 C4,5.5 5,6.5 6.5,7 L8,6 L10,8 L8,10 C4,9.5 0.5,6 0,2 Z"/></svg>987-654-3210</li>
      <li><svg viewBox="0 0 10 10"><rect x="2" y="0" width="6" height="10" rx="1"/></svg>987-654-3210</li>
      <li><svg viewBox="0 0 10 10"><rect x="0" y="2" width="10" height="6.5"/></svg>info@marlow&amp;quince.com</li>
      <li><svg viewBox="0 0 10 10"><circle cx="5" cy="5" r="5"/></svg>www.marlow&amp;quince.com</li>
    </ul>
    <div class="divider"></div>
    <address class="address">Street Name, City Name<br>State Zip Code</address>
  </section>

  <section class="card card--back" aria-label="Card back">
    <p class="back__brand">M &amp; Q</p>
  </section>
</body>
</html>
```